Goodlooking website for a company who is working in the IT consultancy

We want a new website designed in WordPress. You can take www.vantoro.nl as an example. It should be a website with some short blocks of information about the company, nice pictures of our partners and our employees. A job page with a clear filter.

Target Market(s)

B2B

Industry/Entity Type

It Company

Coding

Coded - Design and coding required

Number of Pages Required

5+ page

Font styles to use
Sans Serif

Colors
0455a3
34a7d8

Requirements
Must have
• Check briefing

```html
<!DOCTYPE html>
<html lang="en">
<head>
<meta charset="utf-8">
<title>Norvane – IT Consultancy</title>
<link href="https://fonts.googleapis.com/css2?family=PT+Sans:wght@400;700&family=Montserrat:wght@500;600&family=Source+Sans+3:wght@400;600&display=swap" rel="stylesheet">
<style>
:root{
  --teal:#34a7d8;
  --teal-btn:#3aaec0;
  --teal-dark:#0e4a52;
  --navy:#0455a3;
  --ink:#222;
  --muted:#555;
  --footer:#333333;
  --footer-bar:#3c3c3c;
  --footer-text:#b9b9b9;
  --line:#4a4a4a;
}
*{margin:0;padding:0;box-sizing:border-box}
html,body{width:901px;height:1200px;overflow:hidden;background:#fff}
body{position:relative;font-family:"Source Sans 3",sans-serif;color:var(--ink)}
.abs{position:absolute}

/* header */
.site-header{position:absolute;left:0;top:0;width:901px;height:54px;background:#fff;border-bottom:2px solid #e3e3e3}
.brand{position:absolute;left:120px;top:14px;display:flex;align-items:center;gap:8px;font-family:"PT Sans",sans-serif;font-size:22px;font-weight:400;color:var(--teal-dark);letter-spacing:2px}
.brand-mark{width:22px;height:22px;border-radius:50%;background:var(--teal-dark)}
.main-nav{position:absolute;left:470px;top:0;height:54px;display:flex}
.main-nav a{display:block;height:54px;line-height:54px;padding:0 14px;font-family:"PT Sans",sans-serif;font-size:7.5px;font-weight:700;color:#8a8a8a;text-decoration:none;letter-spacing:.3px}
.main-nav a.active{background:var(--teal-btn);color:#fff}

/* hero */
.hero{position:absolute;left:0;top:55px;width:901px;height:319px;background:linear-gradient(180deg,#3f78b8 0%,#6f9fd0 45%,#a9c3dd 70%,#33466a 85%,#1b2537 100%)}
.hero-rocks{position:absolute;right:0;bottom:0;width:360px;height:230px;background:linear-gradient(160deg,rgba(90,90,90,0) 0%,rgba(80,78,74,.6) 40%,#3b3a38 100%)}
.hero-title{position:absolute;left:125px;top:113px;font-family:"PT Sans",sans-serif;font-weight:700;font-size:30px;line-height:32px;color:#fff;text-transform:uppercase}
.hero-sub{position:absolute;left:126px;top:190px;font-family:"Montserrat",sans-serif;font-weight:500;font-size:12.5px;color:#1d2838}
.btn{position:absolute;display:flex;align-items:center;justify-content:center;gap:5px;border-radius:20px;color:#fff;font-family:"PT Sans",sans-serif;font-weight:700;letter-spacing:.4px;text-transform:uppercase}
.btn .dot{width:7px;height:7px;border:1.3px solid #fff;border-radius:50%}
.btn-hero{left:125px;top:221px;width:116px;height:34px;background:var(--teal-btn);font-size:9px}

/* about */
.about{position:absolute;left:0;top:374px;width:901px;height:348px;background:linear-gradient(100deg,#fbf8f4 0%,#f3f4f6 40%,#dfe7ee 70%,#b9d3e6 100%)}
.eyebrow{position:absolute;left:125px;top:407px;font-family:"PT Sans",sans-serif;font-size:8.5px;letter-spacing:2px;color:var(--teal);font-weight:700}
.about-title{position:absolute;left:125px;top:420px;font-family:"PT Sans",sans-serif;font-weight:700;font-size:21px;color:var(--teal-btn)}
.about-sub{position:absolute;left:126px;top:453px;font-family:"PT Sans",sans-serif;font-weight:700;font-size:11px;letter-spacing:.6px;color:#222}
.about-copy{position:absolute;left:126px;top:488px;width:380px;font-size:9.6px;line-height:18px;color:#333}
.btn-solutions{left:128px;top:619px;width:102px;height:26px;background:var(--teal-btn);font-size:7.8px}
.btn-team{left:238px;top:619px;width:102px;height:26px;background:var(--teal-dark);font-size:7.8px}

.jobs-card{position:absolute;left:551px;top:406px;width:230px;height:284px;background:#fff;box-shadow:0 1px 6px rgba(0,0,0,.12)}
.jobs-card h3{position:absolute;left:15px;top:15px;font-family:"PT Sans",sans-serif;font-size:13px;font-weight:700;color:#222;letter-spacing:.5px}
.job{position:absolute;left:15px;width:201px;height:50px;border-bottom:1px dashed #bbb}
.job-title{position:absolute;left:6px;top:8px;font-size:8.6px;font-weight:600;color:#222}
.job-loc{position:absolute;left:6px;top:28px;display:flex;align-items:center;gap:8px;font-size:8px;color:#666}
.btn-jobs{left:625px;top:655px;width:83px;height:22px;background:#3a3a3a;font-size:6.5px}

/* partners */
.partners-title{position:absolute;left:0;top:743px;width:901px;text-align:center;font-family:"PT Sans",sans-serif;font-weight:700;font-size:15px;color:#222;letter-spacing:.5px}
.partner{position:absolute;top:782px;width:99px;height:68px;border:1px solid #ddd;background:#fff;display:flex;align-items:center;justify-content:center}
.partner span{display:block;width:60px;height:18px;border-radius:3px;background:#c9d3dc}

/* footer */
.site-footer{position:absolute;left:0;top:877px;width:901px;height:259px;background:var(--footer)}
.f-col h4{position:absolute;top:916px;font-family:"PT Sans",sans-serif;font-weight:400;font-size:11px;color:#eee;letter-spacing:.6px}
.f-rule{position:absolute;top:935px;height:1px;background:var(--line)}
.f-rule::before{content:"";position:absolute;left:0;top:-.5px;width:32px;height:2px;background:var(--teal)}
.f-label{position:absolute;font-family:"PT Sans",sans-serif;font-size:9px;color:#eee;letter-spacing:.5px}
.f-text{position:absolute;font-family:"PT Sans",sans-serif;font-size:8.5px;line-height:13.5px;color:var(--footer-text);letter-spacing:.6px}
.f-phone{font-size:12px;letter-spacing:1px}
.f-email{font-size:12px;color:var(--teal);letter-spacing:.5px}
.f-links{position:absolute;list-style:none}
.f-links li{height:24.5px;border-bottom:1px solid #3e3e3e;font-family:"PT Sans",sans-serif;font-size:8.6px;color:var(--footer-text);letter-spacing:.8px;line-height:18px}
.f-links li::before{content:"»";margin-right:9px;color:#777}
.news-input{position:absolute;left:588px;top:985px;width:175px;height:23px;background:#fff;border:none;font-size:8px;padding-left:8px;color:#999;line-height:23px}
.btn-subscribe{left:589px;top:1015px;width:78px;height:22px;background:#4a4a4a;font-family:"Source Sans 3",sans-serif;font-weight:400;text-transform:none;font-size:8.5px;letter-spacing:0;gap:6px}
.footer-bar{position:absolute;left:0;top:1136px;width:901px;height:64px;background:var(--footer-bar)}
.social{position:absolute;top:1148px;width:20px;height:20px;border:1px solid #777;border-radius:50%}
.copyright{position:absolute;left:0;top:1179px;width:901px;text-align:center;font-family:"PT Sans",sans-serif;font-size:8px;color:#8a8a8a;letter-spacing:.8px}
</style>
</head>
<body>

<header class="site-header">
  <div class="brand"><span class="brand-mark"></span>Norvane</div>
  <nav class="main-nav">
    <a class="active">HOME</a>
    <a>OUR SOLUTIONS</a>
    <a>OUR TEAM</a>
    <a>JOBS</a>
    <a>CONTACT</a>
  </nav>
</header>

<section class="hero" role="img" aria-label="Photo of two climbers helping each other up a rocky summit above a blue mountain range">
  <div class="hero-rocks"></div>
</section>
<h1 class="hero-title">Helping IT professionals to<br>achieve their dreams.</h1>
<p class="hero-sub">We Provide World Class IT Training And Personal Coaching.</p>
<div class="btn btn-hero">Contact us <span class="dot"></span></div>

<section class="about" role="img" aria-label="Faded photo of glass office towers seen from below"></section>
<div class="eyebrow">ABOUT US</div>
<h2 class="about-title">Welcome to Norvane</h2>
<p class="about-sub">This is a subheading information about the company</p>
<p class="about-copy">Vestibulum ut ornare elit. Cras dictum faucibus eros at efficitur. Aliquam non tellus a nunc viverra ultricies a vel sem. Nam odio ipsum, porta sit amet sapien nec, sagittis pulvinar massa. Cras sit amet lobortis massa. Donec sit amet nisl sed nulla egestas fermentum. Nulla facilisi. Aliquam sed velit et eros blandit scelerisque vel quis elit. Nunc sit amet nisi quis eros ultricies lobortis sit amet sed purus. Lorem ipsum dolor sit amet, consectetur adipiscing elit.</p>
<div class="btn btn-solutions">Our solutions <span class="dot"></span></div>
<div class="btn btn-team">Meet the team <span class="dot"></span></div>

<aside class="jobs-card">
  <h3>Recent Jobs</h3>
  <div class="job" style="top:47px">
    <div class="job-title">Full Stack Developer</div>
    <div class="job-loc"><svg width="7" height="10" viewBox="0 0 7 10"><path d="M3.5 0A3.5 3.5 0 0 0 0 3.5C0 6 3.5 10 3.5 10S7 6 7 3.5A3.5 3.5 0 0 0 3.5 0zm0 5A1.4 1.4 0 1 1 3.5 2.2 1.4 1.4 0 0 1 3.5 5z" fill="#1aa89a"/></svg>Eindhoven</div>
  </div>
  <div class="job" style="top:97px">
    <div class="job-title">Desktop Support Engineer</div>
    <div class="job-loc"><svg width="7" height="10" viewBox="0 0 7 10"><path d="M3.5 0A3.5 3.5 0 0 0 0 3.5C0 6 3.5 10 3.5 10S7 6 7 3.5A3.5 3.5 0 0 0 3.5 0zm0 5A1.4 1.4 0 1 1 3.5 2.2 1.4 1.4 0 0 1 3.5 5z" fill="#1aa89a"/></svg>Amsterdam</div>
  </div>
  <div class="job" style="top:147px">
    <div class="job-title">Android/Java developer</div>
    <div class="job-loc"><svg width="7" height="10" viewBox="0 0 7 10"><path d="M3.5 0A3.5 3.5 0 0 0 0 3.5C0 6 3.5 10 3.5 10S7 6 7 3.5A3.5 3.5 0 0 0 3.5 0zm0 5A1.4 1.4 0 1 1 3.5 2.2 1.4 1.4 0 0 1 3.5 5z" fill="#1aa89a"/></svg>Eindhoven</div>
  </div>
  <div class="job" style="top:197px">
    <div class="job-title">Technical Support Engineer</div>
    <div class="job-loc"><svg width="7" height="10" viewBox="0 0 7 10"><path d="M3.5 0A3.5 3.5 0 0 0 0 3.5C0 6 3.5 10 3.5 10S7 6 7 3.5A3.5 3.5 0 0 0 3.5 0zm0 5A1.4 1.4 0 1 1 3.5 2.2 1.4 1.4 0 0 1 3.5 5z" fill="#1aa89a"/></svg>Hilversum</div>
  </div>
</aside>
<div class="btn btn-jobs">View all jobs <span class="dot"></span></div>

<h2 class="partners-title">Technology Partners</h2>
<div class="partner" style="left:235px"><span></span></div>
<div class="partner" style="left:345px"><span></span></div>
<div class="partner" style="left:455px"><span></span></div>
<div class="partner" style="left:565px"><span></span></div>

<footer class="site-footer"></footer>
<div class="f-col"><h4 style="left:137px">Contact Info</h4></div>
<div class="f-rule" style="left:137px;width:138px"></div>
<svg class="abs" style="left:139px;top:960px" width="8" height="11" viewBox="0 0 7 10"><path d="M3.5 0A3.5 3.5 0 0 0 0 3.5C0 6 3.5 10 3.5 10S7 6 7 3.5A3.5 3.5 0 0 0 3.5 0zm0 5A1.4 1.4 0 1 1 3.5 2.2 1.4 1.4 0 0 1 3.5 5z" fill="var(--teal)"/></svg>
<div class="f-label" style="left:157px;top:958px">Address:</div>
<div class="f-text" style="left:157px;top:974px">Lindeweg 14,<br>3521 KD Utrecht</div>
<svg class="abs" style="left:139px;top:1016px" width="9" height="10" viewBox="0 0 10 10"><path d="M2 0l2 2.5-1.2 1.5a6 6 0 0 0 3.2 3.2L7.5 6 10 8 8.5 10C4 10 0 6 0 1.5z" fill="var(--teal)"/></svg>
<div class="f-label" style="left:157px;top:1015px">Phone:</div>
<div class="f-text f-phone" style="left:157px;top:1031px">085-3170246</div>
<svg class="abs" style="left:138px;top:1065px" width="11" height="8" viewBox="0 0 11 8"><rect width="11" height="8" rx="1" fill="var(--teal)"/><path d="M0.5 0.8l5 3.8 5-3.8" stroke="#333" fill="none"/></svg>
<div class="f-label" style="left:157px;top:1063px">Email:</div>
<div class="f-text f-email" style="left:157px;top:1079px">info@norvane.nl</div>

<div class="f-col"><h4 style="left:310px">Quick Links</h4></div>
<div class="f-rule" style="left:310px;width:101px"></div>
<ul class="f-links" style="left:311px;top:957px;width:100px">
  <li>Home</li><li>Our Solutions</li><li>Our Team</li><li>Jobs</li><li style="border:none">Contact</li>
</ul>

<div class="f-col"><h4 style="left:446px">Support</h4></div>
<div class="f-rule" style="left:446px;width:108px"></div>
<ul class="f-links" style="left:447px;top:957px;width:107px">
  <li>Terms of Use</li><li>Privacy Policy</li><li style="border:none">Cookie Policy</li>
</ul>

<div class="f-col"><h4 style="left:588px">Join Our Newsletter</h4></div>
<div class="f-rule" style="left:588px;width:175px"></div>
<div class="f-text" style="left:588px;top:960px;font-family:'Source Sans 3',sans-serif;letter-spacing:0">Subscribe for Job Alerts and Updates!</div>
<div class="news-input">Enter Your Email</div>
<div class="btn btn-subscribe"><svg width="9" height="9" viewBox="0 0 10 10"><path d="M10 0L0 4.5l3.5 1.2L4.5 10 6 6.5z" fill="#fff"/></svg>Subscribe</div>

<div class="footer-bar"></div>
<div class="social" style="left:428px"></div>
<div class="social" style="left:452px"></div>
<div class="copyright">Copyright © 2018 NORVANE. All Rights Reserved.</div>

</body>
</html>
```